Website Design for a different kind of Business Consulting organisation needed!

We need a website design that reflects who we are, the simplicity of our consulting business and with a focus on our priority - to help our clients deliver, or execute - the "e" in Vantor-i.

Our key high level requirements are:
1) Simple and intuitive look and feel
2) Integration with all key social media platforms, twitter, facebook, linkedin, tumblr.

10 pages, tops.
- Main page - Welcome
- About Us/ Who are Vantor-i?
- 5 services pages - Project Management, Business Process Management, Change Management, Business Analysis and Finance Systems
- Contact Us

Something like:
http://www.lumvexhold.example/

Vantor-i is a registered trademark and all Logos and other branded material are attached for reference.

So, what’s our gig: A few snippets from previous work...

We are a different kind of business consulting group. We partner with our clients to help them deliver change. We don't just provide them with the theory. We also provide them with the leadership and capability to execute the change.

We aren’t a one stop shop, and we don’t offer cookie cutter solutions. We’re a boutique consulting firm covering Project Management, Business Process Management, Change Management and Business Analytics.

Vantor-i is a professional services organisation that partners with their clients to lead the execution of strategic process and system improvement initiatives. Vantor-i combines hands on delivery with coaching in best practice methodologies and approaches to build their clients capabilities to ensure their ongoing success in project implementations.

UPDATES:

Thanks to everyone who has submitted designs so far. The standard of designs coming through is quite high, with lots of professional designs that nail the design brief. Eliminating them is proving to be quite challenging.

A few updates to the job brief:
- Please make sure the design fits on one page. We would like all of our information to be on the first page that people see without them having to scroll down
- Please ensure you include the FIVE services we offer in the design
- Please use corporate images/istock photos in your designs which are relevant to our business
- Please add a section for a live twitter feed from our twitter account and a link to google+
- Please add a section for news/updates

Also, if you are able to build a site once a design is selected, please let us know.

Thanks,

Maribel.

Target Market(s)

Our target customers are large enterprises in Australia that are growing rapidly and have recently (last 24 months) undertaken or are currently undergoing software implementations and business process improvement programs. These businesses have a turnover of $100m or above and are working hard to differentiate themselves from their competitors but are not seeing the return on investment promised by software vendors and process improvement initiatives.

Industry/Entity Type

Leadership

Requirements
Must have
• Collaboration / Training / Workshop / Consulting images all of a professional nature.
Simple, non-cluttered look with plenty of white space.

```html
<!DOCTYPE html>
<html lang="en">
<head>
<meta charset="utf-8">
<title>Vantor-i | Contact Us</title>
<link rel="stylesheet" href="https://fonts.googleapis.com/css2?family=Open+Sans:ital,wght@0,400;0,600;0,700;1,400&display=swap">
<style>
:root{
  --brand:#0054a6;
  --brand-dark:#004a93;
  --text:#555;
  --heading:#444;
  --muted:#999;
  --rule:#d6d6d6;
  --field-bg:#f9f9f9;
  --field-border:#c8c8c8;
  --icon-grey:#6b6b6b;
  --map-base:#e9e5dc;
  --white:#fff;
}
*{box-sizing:border-box;margin:0;padding:0}
html,body{width:1200px;height:1150px;overflow:hidden}
body{position:relative;background:var(--white);font-family:"Open Sans",Arial,sans-serif;color:var(--text)}
.abs{position:absolute}
.top-band{left:0;top:0;width:1200px;height:6px;background:var(--brand)}
.brand{display:flex;align-items:center;gap:10px;color:var(--brand);font-weight:600;font-size:46px;letter-spacing:-.5px;line-height:1}
.brand-dot{width:26px;height:26px;border-radius:50%;background:var(--brand)}
.site-brand{left:120px;top:34px}
.social{display:flex;gap:9px}
.social span{width:32px;height:32px;border-radius:50%;background:var(--icon-grey)}
.social span.active{background:var(--brand)}
.header-social{left:922px;top:18px}
.main-nav{left:560px;top:72px;display:flex;align-items:center;font-size:15px;font-weight:600;text-transform:uppercase;color:var(--muted)}
.main-nav a{color:inherit;text-decoration:none;padding:0 20px;line-height:22px}
.main-nav a.current{background:var(--brand);color:var(--white);padding:0 16px;margin-left:5px;width:106px}
.rule{height:1px;background:var(--rule)}
.header-rule{left:120px;top:116px;width:960px}
.page-title{left:120px;top:142px;font-size:26px;font-weight:700;color:var(--brand)}
.intro{left:120px;top:175px;width:965px;font-size:16px;line-height:25px}
.section-title{font-size:20px;font-weight:700;color:var(--heading)}
.field-label{font-size:16px;color:var(--heading)}
.field{width:505px;height:33px;background:var(--field-bg);border:1px solid var(--field-border);font-style:italic;font-size:16px;color:#b8b8b8;padding:5px 14px}
.field.focus{border:2px solid var(--brand);padding:4px 13px}
.field.message{height:139px;padding-top:6px;width:504px}
.submit{left:506px;top:739px;width:119px;height:38px;background:var(--brand);color:var(--white);font-size:17px;text-align:center;line-height:38px}
.map{left:691px;top:345px;width:386px;height:360px;border:1px solid #ccc;background:linear-gradient(160deg,#ece8df 0%,#e6e2d8 55%,#dfe3d0 100%)}
.details-rule{left:120px;top:887px;width:960px}
.detail{font-size:16px;line-height:25px}
.icon-line{display:flex;align-items:center;gap:9px;height:30px}
.icon-line svg{flex:none}
.footer{left:0;top:1025px;width:1200px;height:125px;background:var(--brand);color:var(--white)}
.footer h3{font-size:13px;font-weight:700;text-transform:uppercase;margin-bottom:2px}
.footer p,.footer li{font-size:12px;line-height:19px;list-style:none}
.footer .social span{background:var(--white);width:33px;height:33px}
.footer-brand{left:868px;top:22px;color:var(--white);font-size:40px}
.footer-brand .brand-dot{background:var(--white);width:24px;height:24px}
</style>
</head>
<body>
<div class="abs top-band"></div>

<header>
  <div class="abs brand site-brand">Vantor-i<span class="brand-dot"></span></div>
  <div class="abs social header-social" aria-label="Social networks">
    <span></span><span></span><span></span><span class="active"></span>
  </div>
  <nav class="abs main-nav">
    <a href="#">Home</a><a href="#">About</a><a href="#">Services</a><a href="#">Partners</a><a href="#" class="current">Contact</a>
  </nav>
  <div class="abs rule header-rule"></div>
</header>

<main>
  <h1 class="abs page-title">Contact Us</h1>
  <p class="abs intro">Sed ut perspiciatis unde omnis iste natus error sit voluptatem accusantium doloremque laudantium, totam rem aperiam, eaque ipsa quae ab illo inventore veritatis et quasi architecto beatae vitae dicta sunt explicabo.</p>

  <h2 class="abs section-title" style="left:115px;top:286px">Contact Form</h2>
  <div class="abs field-label" style="left:122px;top:321px">Name:</div>
  <div class="abs field" style="left:121px;top:346px">Enter you name</div>
  <div class="abs field-label" style="left:122px;top:393px">Email Address:</div>
  <div class="abs field focus" style="left:120px;top:417px;width:506px;height:35px">Enter your email</div>
  <div class="abs field-label" style="left:122px;top:468px">Subject:</div>
  <div class="abs field" style="left:121px;top:493px">Enter subject</div>
  <div class="abs field-label" style="left:122px;top:542px">Message:</div>
  <div class="abs field message" style="left:121px;top:567px">Enter Message</div>
  <div class="abs submit">Submit</div>

  <h2 class="abs section-title" style="left:694px;top:286px">Location Map</h2>
  <div class="abs map" role="img" aria-label="Street map of the office location with a marker"></div>

  <h2 class="abs section-title" style="left:124px;top:847px">Contact Details</h2>
  <div class="abs rule details-rule"></div>
  <p class="abs detail" style="left:124px;top:902px">Level 8, 42 Harbour Ln. Melbourne<br>Australia, 3000</p>

  <div class="abs detail" style="left:485px;top:900px">
    <div class="icon-line">
      <svg width="23" height="23" viewBox="0 0 24 24" aria-hidden="true"><circle cx="12" cy="12" r="12" fill="var(--brand)"/><path d="M6 9c0-2 3-3 6-3s6 1 6 3v1h-3V9H9v1H6z M8 12h8l2 6H6z" fill="#fff"/></svg>
      <span>+61 3 5550 4127</span>
    </div>
    <div class="icon-line">
      <svg width="23" height="23" viewBox="0 0 24 24" aria-hidden="true"><circle cx="12" cy="12" r="12" fill="var(--brand)"/><rect x="8" y="5" width="8" height="5" fill="#fff"/><rect x="5" y="10" width="14" height="6" rx="1" fill="#fff"/><rect x="8" y="14" width="8" height="5" fill="#fff" stroke="var(--brand)"/></svg>
      <span>+61 3 5550 9836</span>
    </div>
  </div>

  <div class="abs detail" style="left:778px;top:900px">
    <div class="icon-line">
      <svg width="23" height="23" viewBox="0 0 24 24" aria-hidden="true"><circle cx="12" cy="12" r="12" fill="var(--brand)"/></svg>
      <span>@vantor-i</span>
    </div>
    <div class="icon-line">
      <svg width="23" height="23" viewBox="0 0 24 24" aria-hidden="true"><circle cx="12" cy="12" r="12" fill="var(--brand)"/><rect x="5" y="7" width="14" height="10" fill="#fff"/><path d="M5 7l7 6 7-6" fill="none" stroke="var(--brand)" stroke-width="1.5"/></svg>
      <span>info@vantor-i.example</span>
    </div>
  </div>
</main>

<footer class="abs footer">
  <div class="abs" style="left:121px;top:20px">
    <h3>Connect with us</h3>
    <p>on social media network</p>
    <div class="social" style="margin-top:6px;gap:7px"><span></span><span></span><span></span><span></span></div>
  </div>
  <div class="abs" style="left:331px;top:20px">
    <h3>Pages</h3>
    <ul><li>Home</li><li>About</li><li>Services</li></ul>
  </div>
  <ul class="abs" style="left:405px;top:39px"><li>Term &amp; Conditions</li><li>FAQ</li><li>Partners</li></ul>
  <div class="abs" style="left:569px;top:20px">
    <h3>Contact Details</h3>
    <p>p: +61 3 5550 4127&nbsp; f: +61 3 5550 9836<br>Level 8, 42 Harbour Ln. Melbourne,<br>Australia, 3000</p>
  </div>
  <div class="abs brand footer-brand">Vantor-i<span class="brand-dot"></span></div>
  <p class="abs" style="left:869px;top:73px">Copyright © 2014 All Rights Reserved</p>
</footer>
</body>
</html>
```